Visit card

Industry/Entity Type

Health Care

Contact Information for Business Card

O VITALIS SYSTEMS
Odile Brevard - chef de Projet

Requirements
Must have
• 318 Gaston Lemaire Street 59710 BÉTHUNE Tel: 33 (0) 327 481 605 Mobile: 06 42 19 37 64 Web: www.quorvexsystems.example Contact: o.brevard@o-vitalissystems.example
Should not have
• Respect for color

```html
<!DOCTYPE html>
<html lang="fr">
<head>
<meta charset="utf-8">
<title>O Vitalis Systems — Carte de visite</title>
<link rel="stylesheet" href="https://fonts.googleapis.com/css2?family=Arimo:wght@400;700&display=swap">
<style>
  :root {
    --page: #e6e6e8;
    --card-white: #ffffff;
    --card-dark: #47474a;
    --ink: #3a3a3c;
    --ink-soft: #4a4a4d;
    --accent: #e42129;
    --emboss: #5a5a5e;
  }
  * { box-sizing: border-box; margin: 0; padding: 0; }
  html, body { width: 1200px; height: 800px; overflow: hidden; }
  body {
    background: var(--page);
    font-family: "Arimo", Arial, sans-serif;
    color: var(--ink);
    display: flex;
    flex-direction: column;
    align-items: center;
    justify-content: center;
    gap: 36px;
  }
  .card {
    width: 620px;
    height: 354px;
    border-radius: 22px;
    position: relative;
    overflow: hidden;
    box-shadow: 0 6px 18px rgba(0,0,0,.18);
  }

  /* Back */
  .card-back {
    background: var(--card-dark);
    display: flex;
    align-items: center;
    justify-content: center;
    gap: 22px;
  }
  .card-back .mark-circle {
    width: 84px; height: 84px;
    border-radius: 50%;
    border: 10px solid var(--emboss);
  }
  .card-back .brand-name {
    font-weight: 700;
    font-size: 34px;
    line-height: 1.05;
    letter-spacing: 2px;
    color: var(--emboss);
  }

  /* Front */
  .card-front { background: var(--card-white); }
  .front-info {
    position: absolute;
    left: 40px;
    top: 44px;
    width: 340px;
  }
  .front-info .brand-name {
    font-weight: 700;
    font-size: 30px;
    line-height: 1.05;
    letter-spacing: 1px;
    color: var(--accent);
    margin-bottom: 26px;
  }
  .person {
    font-size: 17px;
    margin-bottom: 6px;
  }
  .person-name { font-weight: 700; color: var(--ink); letter-spacing: .3px; }
  .person-role { color: var(--accent); }
  .person-role::before { content: "|"; margin: 0 7px 0 6px; }
  .address {
    font-size: 15px;
    line-height: 1.3;
    color: var(--ink-soft);
    margin-bottom: 10px;
  }
  .contact-list { list-style: none; font-size: 14.5px; color: var(--ink-soft); }
  .contact-list li {
    display: flex;
    align-items: center;
    gap: 8px;
    line-height: 1.45;
  }
  .contact-list svg { width: 16px; height: 16px; flex: none; }
  .web {
    margin-top: 6px;
    font-size: 15px;
    color: var(--ink);
  }
  .web .web-domain { color: var(--accent); }
  .front-mark {
    position: absolute;
    right: 48px;
    top: 50%;
    transform: translateY(-50%);
    width: 210px; height: 210px;
    border-radius: 50%;
    border: 26px solid var(--ink);
  }
</style>
</head>
<body>

  <section class="card card-back" aria-label="Verso de la carte">
    <div class="mark-circle"></div>
    <div class="brand-name">O VITALIS<br>SYSTEMS</div>
  </section>

  <section class="card card-front" aria-label="Recto de la carte">
    <div class="front-info">
      <div class="brand-name">O VITALIS<br>SYSTEMS</div>
      <p class="person"><span class="person-name">ODILE BREVARD</span><span class="person-role">Manager</span></p>
      <p class="address">318 Gaston Lemaire Street<br>59710 BÉTHUNE</p>
      <ul class="contact-list">
        <li>
          <svg viewBox="0 0 16 16" aria-hidden="true"><circle cx="8" cy="8" r="7" fill="none" stroke="#e42129" stroke-width="1.4"/><path d="M5.3 4.6l1.4-.3.7 1.7-.9.7a5 5 0 0 0 2.4 2.4l.7-.9 1.7.7-.3 1.4c-3.2.2-5.9-2.5-5.7-5.7z" fill="#e42129"/></svg>
          33 (0) 327 481 605
        </li>
        <li>
          <svg viewBox="0 0 16 16" aria-hidden="true"><circle cx="8" cy="8" r="7" fill="none" stroke="#e42129" stroke-width="1.4"/><rect x="5.8" y="4" width="4.4" height="8" rx=".8" fill="none" stroke="#e42129" stroke-width="1.2"/></svg>
          06 42 19 37 64
        </li>
        <li>
          <svg viewBox="0 0 16 16" aria-hidden="true"><circle cx="8" cy="8" r="7" fill="none" stroke="#e42129" stroke-width="1.4"/><rect x="4.5" y="5.5" width="7" height="5" fill="#e42129"/><path d="M4.5 5.5L8 8.3l3.5-2.8" fill="none" stroke="#fff" stroke-width=".9"/></svg>
          o.brevard@o-vitalissystems.example
        </li>
      </ul>
      <p class="web">www.<span class="web-domain">quorvexsystems</span>.example</p>
    </div>
    <div class="front-mark"></div>
  </section>

</body>
</html>
```